Harwick Moss Fine Art gallery website - Modern british art for sale

We need a website design that is both current and high end. Our products are expensive and this should be reflected in the look of the website. We would like the logo we had designed last year to be clearly seen in the design. We want sleek, simple, and easy to navigate. Nothing too colourful as the colours of the art should always take precedence.

Target Market(s)

The average price of one our products starts at £250 and can go up to £10,000 we are an entry level gallery.

Industry/Entity Type

Art Gallery

Number of Pages Required

5+ page

Font styles to use
Sans Serif

Colors
000000
ffffff
faa54b
abd037
886aae
b868aa

Requirements
Must have
• Attractive front page. Linked to our Twitter feed.
• 4 links from front page - New Releases, about us, Artists, contact us
• Social media links - Facebook, Twitter, YouTube, Instagram.
• Each artist must have their own page, each page must have a biography link to another page.
Nice to have
• Utilise our new logo design. I would like the Twitter feed to link to the front page in a small way so you can see what's being said on Twitter by the company. For future proofing maybe have a locations function on the front page which can be adroit down menu showing where our other galleries are.

```html
<!DOCTYPE html>
<html lang="en">
<head>
<meta charset="utf-8">
<title>Harwick Moss Fine Art — Gallery</title>
<link rel="stylesheet" href="https://fonts.googleapis.com/css2?family=Cinzel:wght@400;700&family=Lato:wght@400;700&display=swap">
<style>
:root{
  --header-bg:#23272b;
  --panel:#2d3337;
  --footer-bg:#2a2d30;
  --text:#ffffff;
  --muted:#e6e6e6;
  --gold:#d9b24a;
  --page-top:#8a847a;
  --page-mid:#6e6a66;
  --page-low:#7d7870;
}
*{box-sizing:border-box;margin:0;padding:0}
html,body{width:1200px;height:1001px;overflow:hidden}
body{position:relative;font-family:'Lato',sans-serif;color:var(--text);background:var(--page-mid)}
.backdrop{position:absolute;left:0;top:116px;width:1200px;height:827px;
  background:linear-gradient(180deg,var(--page-top) 0%,#7a7670 25%,var(--page-mid) 55%,var(--page-low) 100%)}
.site-header{position:absolute;left:0;top:0;width:1200px;height:116px;
  background:radial-gradient(ellipse at 12% 30%,#3e4347 0%,var(--header-bg) 55%,#1b1e21 100%)}
.brand{position:absolute;left:80px;top:62px;display:flex;align-items:center;gap:10px}
.brand-mark{width:14px;height:14px;border-radius:50%;background:var(--gold)}
.brand-name{font-family:'Cinzel',serif;font-weight:400;font-size:27px;line-height:30px;color:var(--gold);letter-spacing:.5px}
.header-contact{position:absolute;top:18px;right:80px;display:flex;align-items:center;font-size:16px}
.header-contact .item{display:flex;align-items:center;gap:18px;margin-left:30px}
.header-contact svg{width:28px;height:28px}
.main-nav{position:absolute;top:76px;right:80px;display:flex;gap:62px}
.main-nav a{font-family:'Cinzel',serif;font-size:14.5px;line-height:18px;color:var(--text);text-decoration:none;letter-spacing:.5px;text-transform:uppercase}
.gallery-panel{position:absolute;left:80px;top:199px;width:585px;height:623px;background:var(--panel)}
.gallery-panel::after{content:"";position:absolute;left:63px;bottom:-13px;border-left:13px solid transparent;border-top:13px solid var(--panel)}
.gallery-title{position:absolute;left:18px;top:24px;font-family:'Cinzel',serif;font-weight:700;font-size:24px;letter-spacing:.5px}
.gallery-art{position:absolute;left:20px;top:69px;width:546px;height:441px;
  background:linear-gradient(180deg,#f2eee8 0%,#e7dfd6 40%,#4a4644 70%,#c9502a 100%)}
.gallery-caption{position:absolute;left:22px;top:531px;width:540px;font-size:14.5px;line-height:21.5px;color:var(--muted)}
.feature-panel{position:absolute;left:720px;top:199px;width:400px;height:368px;background:var(--panel)}
.feature-art{position:absolute;left:14px;top:16px;width:372px;height:336px;
  background:radial-gradient(ellipse at 60% 40%,#d8d8d8 0%,#f6f6f6 60%,#ffffff 100%)}
.info-tag{position:absolute;left:18px;top:319px;height:24px;padding:0 8px;background:#1f2224;
  font-size:14px;font-weight:700;display:flex;align-items:center;gap:12px}
.contact-panel{position:absolute;left:720px;top:596px;width:400px;height:231px;background:var(--panel)}
.contact-list{list-style:none;position:absolute;left:34px;top:26px}
.contact-list li{display:flex;align-items:flex-start;gap:12px;font-size:13.5px;line-height:20px;color:var(--muted)}
.contact-list svg{width:30px;height:30px;flex:none}
.pager{position:absolute;left:82px;top:860px;display:flex}
.pager a{width:31px;height:30px;border:1px solid #e8e8e8;color:var(--text);text-decoration:none;
  display:flex;align-items:center;justify-content:center;font-size:14px;margin-right:13px}
.pager a.current{background:#9a9a9a}
.pager a.pause{font-size:18px}
.site-footer{position:absolute;left:0;top:943px;width:1200px;height:58px;background:var(--footer-bg)}
.copyright{position:absolute;left:83px;top:22px;font-size:14px}
.social{position:absolute;right:80px;top:17px;display:flex;gap:10px}
.social a{width:28px;height:28px;background:#5a5e62;border-radius:2px;display:block}
</style>
</head>
<body>
<div class="backdrop" role="img" aria-label="Soft pastel street painting used as page background"></div>

<header class="site-header">
  <div class="brand"><span class="brand-mark"></span><span class="brand-name">Harwick Moss Fine Art</span></div>
  <div class="header-contact">
    <div class="item">
      <svg viewBox="0 0 30 30"><circle cx="15" cy="15" r="13.5" fill="none" stroke="#fff" stroke-width="1.5"/><circle cx="15" cy="15" r="9" fill="none" stroke="#fff" stroke-width="1.5"/><path d="M15 9v6h4" fill="none" stroke="#fff" stroke-width="1.5"/></svg>
      <span>10:00 am-6:00 pm</span>
    </div>
    <div class="item">
      <svg viewBox="0 0 30 30"><circle cx="15" cy="15" r="13.5" fill="none" stroke="#fff" stroke-width="1.5"/><path d="M10 9c1-1 2-1 2.5 0l1.3 2.3c.4.7 0 1.3-.6 1.8 .8 1.8 2 3 3.8 3.8.5-.6 1.1-1 1.8-.6l2.3 1.3c1 .5 1 1.5 0 2.5-2 2-6 .5-9-2.5S8 11 10 9z" fill="#fff"/></svg>
      <span>123-456-7890</span>
    </div>
  </div>
  <nav class="main-nav">
    <a href="#">New Releases</a>
    <a href="#">About Us</a>
    <a href="#">Artists</a>
    <a href="#">Locations</a>
  </nav>
</header>

<main>
  <section class="gallery-panel">
    <h1 class="gallery-title">GALLERY</h1>
    <div class="gallery-art" role="img" aria-label="Artwork: crayon drawing of a dark church tower beside an orange building under a scribbled sky"></div>
    <p class="gallery-caption">Lorem ipsum dolor sit amet, consectetuer adipiscing elit, sed adipiscing elit, sed diam nonummy nibh euismod tincidunt sed diam nonu mmy nibhop euismod tincidunt ut lao reet dolore magna aliquam</p>
  </section>

  <section class="feature-panel">
    <div class="feature-art" role="img" aria-label="Artwork: black ink line etching on white"></div>
    <div class="info-tag"><span>+</span><span>info</span></div>
  </section>

  <section class="contact-panel">
    <ul class="contact-list">
      <li style="margin-bottom:12px">
        <svg viewBox="0 0 30 30"><circle cx="15" cy="15" r="13.5" fill="none" stroke="#fff" stroke-width="1.5"/><path d="M15 8a4.5 4.5 0 0 1 4.5 4.5C19.5 16 15 22 15 22s-4.5-6-4.5-9.5A4.5 4.5 0 0 1 15 8z" fill="#fff"/><circle cx="15" cy="12.5" r="1.6" fill="#2d3337"/></svg>
        <span>Lorem ipsum, Dollar smit City<br>Code - 1234</span>
      </li>
      <li style="margin-bottom:16px">
        <svg viewBox="0 0 30 30"><circle cx="15" cy="15" r="13.5" fill="none" stroke="#fff" stroke-width="1.5"/><path d="M10 9c1-1 2-1 2.5 0l1.3 2.3c.4.7 0 1.3-.6 1.8 .8 1.8 2 3 3.8 3.8.5-.6 1.1-1 1.8-.6l2.3 1.3c1 .5 1 1.5 0 2.5-2 2-6 .5-9-2.5S8 11 10 9z" fill="#fff"/></svg>
        <span>123 456 7890</span>
      </li>
      <li style="margin-bottom:16px">
        <svg viewBox="0 0 30 30"><circle cx="15" cy="15" r="13.5" fill="none" stroke="#fff" stroke-width="1.5"/><rect x="9" y="11" width="12" height="8" fill="#fff"/><path d="M9 11l6 5 6-5" fill="none" stroke="#2d3337" stroke-width="1.2"/></svg>
        <span>info@harwickmossart.com</span>
      </li>
      <li>
        <svg viewBox="0 0 30 30"><circle cx="15" cy="15" r="13.5" fill="none" stroke="#fff" stroke-width="1.5"/><circle cx="15" cy="15" r="9" fill="none" stroke="#fff" stroke-width="1.5"/><path d="M15 9v6h4" fill="none" stroke="#fff" stroke-width="1.5"/></svg>
        <span>10:00 am To 6:00 pm</span>
      </li>
    </ul>
  </section>

  <nav class="pager">
    <a href="#">1</a>
    <a href="#" class="current">2</a>
    <a href="#">3</a>
    <a href="#">4</a>
    <a href="#">5</a>
    <a href="#" class="pause" aria-label="Pause">||</a>
  </nav>
</main>

<footer class="site-footer">
  <p class="copyright">Copyright ©&nbsp; 2017&nbsp; Harwick Moss Fine Arts. All Rights&nbsp; Reserved</p>
  <div class="social">
    <a href="#" aria-label="Social profile 1"></a>
    <a href="#" aria-label="Social profile 2"></a>
    <a href="#" aria-label="Social profile 3"></a>
    <a href="#" aria-label="Video channel"></a>
  </div>
</footer>
</body>
</html>
```